Fitness website

Website for a fitness brand (see attached specs). Design needs to be modern and vibrant with CTAs on every page. We will provide logos, images, etc but for now user placeholder text and images. For now use the name 'Corvane Athletics' as the name to use on the design. The goal of this site is to either get people to join the gym (5 physical locations across the US); buy an online program; buy merch or supplements or sign up for the newsletter. Pleas use images from this foldeR: https://filebarn.example/share/folders/8QwTz41mKpLrXv93NdYe7HsaBuJ0Cf2_R?usp=sharing

We will be coding this in ReactNative. Lots more work for the winner as well, this is a 1st project for us.

Target Market(s)

fitness enthusiats

Industry/Entity Type

fitness, health, wellness

Number of Pages Required

5+ page

Font styles to use
Other font styles liked:
• Lato

Colors
0054AA
0677BA
7BADD7
CADEEF
E8F1F8
0094D4
00A9DD
6FCCEA
C7EBF8
E9F6FB
00AB8E
00BBA5
67D7C9
C6EFE9
E9F9F6
EE7325
F08F49
F5BC92
FAE3D3
FDF4ED

Requirements
Must have
• must be reactive. most people will view it first on mobile
Nice to have
• video in hero section of top of home page

```html
<!DOCTYPE html>
<html lang="en">
<head>
<meta charset="utf-8">
<title>Corvane Athletics — Home</title>
<link href="https://fonts.googleapis.com/css2?family=Barlow:wght@500;600;700;800&family=Roboto:wght@400;500;700&display=swap" rel="stylesheet">
<style>
:root{
  --blue-900:#0054AA;--blue-700:#0677BA;--blue-300:#7BADD7;--blue-100:#CADEEF;--blue-50:#E8F1F8;
  --sky:#0094D4;--sky-2:#00A9DD;--teal:#00AB8E;--teal-2:#00BBA5;
  --orange:#EE7325;--orange-2:#F08F49;--ink:#1b1d22;--muted:#555c66;--white:#fff;
}
*{box-sizing:border-box;margin:0;padding:0}
html,body{width:1200px;height:4902px;overflow:hidden}
body{position:relative;font-family:"Roboto",sans-serif;color:var(--ink);background:#fff}
.abs{position:absolute}
.eyebrow{font-family:"Barlow",sans-serif;font-weight:700;font-size:13px;color:var(--blue-900);text-transform:uppercase;letter-spacing:.6px}
.title{font-family:"Barlow",sans-serif;font-weight:700;font-size:38px;text-transform:uppercase;letter-spacing:.5px;line-height:1.05}
.center{left:0;width:1200px;text-align:center}
.btn{position:absolute;display:flex;align-items:center;justify-content:center;gap:6px;border-radius:22px;font-family:"Barlow",sans-serif;font-weight:700;font-size:13px;text-transform:uppercase;color:#fff;background:linear-gradient(180deg,var(--orange-2),var(--orange));letter-spacing:.4px}
.btn-ghost{background:transparent;border:2px solid #fff}
.ph{position:absolute}

.nav{top:0;left:0;width:1200px;height:72px;background:#fff;display:flex;align-items:center;padding:0 46px}
.brand{font-family:"Barlow",sans-serif;font-weight:700;font-size:21px;color:var(--blue-900);text-transform:uppercase}
.menu{display:flex;gap:40px;margin-left:46px;font-family:"Barlow",sans-serif;font-weight:600;font-size:13px;text-transform:uppercase}
.menu .on{color:var(--orange);border-bottom:2px solid var(--orange);padding-bottom:4px}
.nav .btn{right:52px;top:15px;width:128px;height:38px}

.hero{top:72px;left:0;width:1200px;height:690px;background:linear-gradient(115deg,#20252c 0%,#3a4350 30%,#1d5a92 55%,#10325e 75%,#2a2f38 100%)}
.hero-kicker{top:203px;font-family:"Barlow",sans-serif;font-weight:600;font-size:25px;color:#fff;letter-spacing:4px}
.hero-title{top:240px;font-family:"Barlow",sans-serif;font-weight:800;font-size:64px;line-height:58px;color:#fff;text-transform:uppercase}
.hero-sub{top:372px;font-size:15px;line-height:19px;color:#fff}

.ghost-word{font-family:"Barlow",sans-serif;font-weight:800;font-size:110px;color:transparent;-webkit-text-stroke:1px #eceff3;letter-spacing:6px}
.prog{position:absolute;top:898px;width:314px;height:356px}
.prog .img{position:absolute;left:0;top:0;width:314px;height:242px}
.prog .card{position:absolute;left:23px;top:184px;width:268px;height:170px;filter:drop-shadow(0 6px 8px rgba(0,0,0,.12))}
.prog .icon{position:absolute;left:129px;top:160px;width:56px;height:56px;border-radius:50%;display:flex;align-items:center;justify-content:center}
.prog h3{position:absolute;top:244px;left:0;width:314px;text-align:center;font-family:"Barlow",sans-serif;font-weight:600;font-size:19px;text-transform:uppercase}
.prog p{position:absolute;top:274px;left:52px;width:210px;text-align:center;font-size:11.5px;line-height:17px;color:var(--muted)}
.prog .dot{position:absolute;left:146px;top:340px;width:22px;height:22px;border-radius:50%;display:flex;align-items:center;justify-content:center}

.prod{position:absolute;top:2159px;width:310px;height:340px;border:1px solid #e1e4e8;border-radius:4px;background:linear-gradient(125deg,#e9ebee 0%,#fafbfc 35%,#e3e6ea 45%,#f7f8f9 70%,#e6e8eb 100%)}
.prod .ph{left:80px;top:28px;width:150px;height:190px;border-radius:8px}
.prod h3{position:absolute;top:238px;width:100%;text-align:center;font-family:"Barlow",sans-serif;font-weight:600;font-size:19px}
.prod p{position:absolute;top:265px;width:100%;text-align:center;font-size:11.5px;color:var(--muted);text-transform:uppercase}
.prod .price{position:absolute;top:287px;width:100%;text-align:center;font-family:"Barlow",sans-serif;font-weight:700;font-size:22px;color:var(--sky)}

.loc{top:2640px;left:0;width:1200px;height:712px;background:linear-gradient(90deg,var(--blue-900) 0%,var(--blue-700) 45%,var(--teal-2) 85%,var(--teal) 100%)}
.diamond{position:absolute;width:210px;height:210px;transform:rotate(45deg);border-radius:6px;overflow:hidden}
.loc-name{position:absolute;width:200px;text-align:center;font-family:"Barlow",sans-serif;font-weight:700;font-size:19px;color:#fff;text-transform:uppercase}

.blog-big{position:absolute;left:106px;top:3524px;width:495px;height:457px;border:1px solid #dfe2e6;background:linear-gradient(135deg,#f6f7f8,#e9ebee)}
.blog-sm{position:absolute;left:614px;width:495px;height:221px;border:1px solid #dfe2e6;background:#fff}
.date{position:absolute;height:22px;padding:0 8px;display:flex;align-items:center;gap:5px;background:var(--blue-900);color:#fff;font-size:11px;font-family:"Barlow",sans-serif;font-weight:600}
.blog-title{position:absolute;font-family:"Barlow",sans-serif;font-weight:700;font-size:19px;line-height:23px;text-transform:uppercase}
.blog-desc{position:absolute;font-size:11px;line-height:16px;color:var(--muted)}

.news{top:4070px;left:0;width:1200px;height:400px;background:linear-gradient(90deg,#eceff3,#f5f6f8 50%,#e9ecf0)}
.input{position:absolute;left:259px;top:4264px;width:509px;height:59px;background:#fff;border:1px solid #d5d9de;font-size:15px;padding:0 26px;display:flex;align-items:center}
.subscribe{position:absolute;left:774px;top:4264px;width:181px;height:59px;background:var(--blue-900);color:#fff;font-family:"Barlow",sans-serif;font-weight:700;font-size:15px;text-transform:uppercase;display:flex;align-items:center;justify-content:center;gap:8px}

.foot-h{font-family:"Barlow",sans-serif;font-weight:600;font-size:19px;color:#fff;text-transform:uppercase}
.foot-list{list-style:none;font-size:14px;color:#e7eef8;line-height:27px}
.foot-list li::before{content:"» ";color:#cfe0f2}
.social{display:flex;align-items:center;gap:14px;font-size:14px;color:#fff;height:46px}
.social i{width:26px;height:26px;border-radius:50%;background:#fff;display:block}
</style>
</head>
<body>

<header class="nav abs">
  <div class="brand">Corvane Athletics</div>
  <nav class="menu">
    <span class="on">Home</span><span>About Us</span><span>Programs</span><span>Shop</span><span>Locations</span><span>Affiliate</span><span>Blog</span><span>Members</span>
  </nav>
  <a class="btn">Contact ›</a>
</header>

<section class="hero abs" role="img" aria-label="Hero video still: male and female athletes training intensely on rowing and jump-rope in a dark gym with blue lighting"></section>
<div class="abs center hero-kicker">CORVANE ATHLETICS</div>
<h1 class="abs center hero-title">Unleash Your<br>Inner Champion</h1>
<p class="abs center hero-sub">Transform your body, sharpen your mind, and join a community<br>built for strength and performance.</p>
<a class="btn" style="left:422px;top:434px;width:174px;height:43px">Join the Gym ›</a>
<a class="btn btn-ghost" style="left:606px;top:434px;width:174px;height:43px">Buy Program ›</a>
<svg class="abs" style="left:0;top:600px" width="1200" height="170" viewBox="0 0 1200 170">
  <polygon points="0,150 600,28 1200,150 1200,170 0,170" fill="#fff"/>
  <polygon points="574,20 626,20 626,60 600,76 574,60" fill="#fff"/>
  <path d="M600 35 v22 M591 49 l9 9 l9 -9" stroke="#0054AA" stroke-width="2.5" fill="none" stroke-linecap="round"/>
</svg>

<div class="abs center ghost-word" style="top:712px">PROGRAMS</div>
<div class="abs center eyebrow" style="top:763px">Choose your path to greatness</div>
<h2 class="abs center title" style="top:793px">Our Training Programs</h2>

<svg class="abs" style="left:30px;top:1003px" width="30" height="56"><path d="M24 4 L6 28 L24 52" stroke="#0677BA" stroke-width="3" fill="none"/></svg>
<svg class="abs" style="left:1136px;top:1003px" width="30" height="56"><path d="M6 4 L24 28 L6 52" stroke="#0677BA" stroke-width="3" fill="none"/></svg>

<div class="prog" style="left:106px">
  <div class="ph img" role="img" aria-label="Photo: masters athlete lifting a loaded barbell" style="background:linear-gradient(135deg,#3b4756,#1f3957 60%,#5a6778)"></div>
  <svg class="card" viewBox="0 0 268 170"><polygon points="0,28 134,0 268,28 268,168 0,168" fill="#fff"/><rect x="0" y="166" width="268" height="3" fill="#0054AA"/></svg>
  <div class="icon" style="background:var(--sky)"><svg width="26" height="26" viewBox="0 0 26 26"><path d="M4 20 C4 12 8 6 13 6 l2 4 h-3 c2 3 7 2 9 6 v4 z" fill="#fff"/></svg></div>
  <h3>Masters</h3>
  <p>Lorem ipsum dolor sit amet, con-sectetur adipiscing elit sed</p>
  <div class="dot" style="background:var(--blue-900)"><svg width="10" height="10"><path d="M3 1 l4 4 l-4 4" stroke="#fff" stroke-width="2" fill="none"/></svg></div>
</div>
<div class="prog" style="left:445px">
  <div class="ph img" role="img" aria-label="Photo: athlete doing functional floor training" style="background:linear-gradient(135deg,#2f3640,#55606b 50%,#2b3d52)"></div>
  <svg class="card" viewBox="0 0 268 170"><polygon points="0,28 134,0 268,28 268,168 0,168" fill="#fff"/><rect x="0" y="166" width="268" height="3" fill="#EE7325"/></svg>
  <div class="icon" style="background:var(--orange)"><svg width="28" height="18" viewBox="0 0 28 18"><path d="M2 6v6M6 2v14M22 2v14M26 6v6M6 9h16" stroke="#fff" stroke-width="3" fill="none"/></svg></div>
  <h3>Functional Fitness</h3>
  <p>Lorem ipsum dolor sit amet, con-sectetur adipiscing elit sed</p>
  <div class="dot" style="background:var(--orange)"><svg width="10" height="10"><path d="M3 1 l4 4 l-4 4" stroke="#fff" stroke-width="2" fill="none"/></svg></div>
</div>
<div class="prog" style="left:787px">
  <div class="ph img" role="img" aria-label="Photo: healthy meal bowl with vegetables and grains" style="background:linear-gradient(135deg,#6d8a3f,#c9b56a 50%,#4f6a3a)"></div>
  <svg class="card" viewBox="0 0 268 170"><polygon points="0,28 134,0 268,28 268,168 0,168" fill="#fff"/><rect x="0" y="166" width="268" height="3" fill="#0677BA"/></svg>
  <div class="icon" style="background:var(--sky)"><svg width="22" height="26" viewBox="0 0 22 26"><rect x="3" y="4" width="16" height="20" rx="2" fill="none" stroke="#fff" stroke-width="2.5"/><path d="M7 11h8M7 16h8" stroke="#fff" stroke-width="2"/></svg></div>
  <h3>Nutritions</h3>
  <p>Lorem ipsum dolor sit amet, con-sectetur adipiscing elit sed</p>
  <div class="dot" style="background:var(--blue-900)"><svg width="10" height="10"><path d="M3 1 l4 4 l-4 4" stroke="#fff" stroke-width="2" fill="none"/></svg></div>
</div>

<section class="abs" style="left:0;top:1373px;width:1200px;height:600px;background:var(--blue-50)"></section>
<svg class="abs" style="left:0;top:1373px" width="640" height="600" viewBox="0 0 640 600">
  <polygon points="456,0 495,0 645,300 495,600 456,600 605,300" fill="#fff"/>
  <polyline points="470,0 622,300 470,600" fill="none" stroke="#0054AA" stroke-width="3"/>
</svg>
<div class="ph" role="img" aria-label="Photo: athlete pushing hard on an air bike in a crowded gym" style="left:0;top:1373px;width:608px;height:600px;clip-path:polygon(0 0,456px 0,605px 300px,456px 600px,0 600px);background:linear-gradient(120deg,#3a3f46,#6b6f74 45%,#2b2f35)"></div>
<div class="abs eyebrow" style="left:639px;top:1484px">Built for athletes. Designed for everyone.</div>
<h2 class="abs title" style="left:639px;top:1510px">About Corvane<br>Athletics</h2>
<p class="abs" style="left:649px;top:1616px;width:500px;font-size:17px;line-height:27px;color:#2e3440">Corvane Athletics is more than a gym — it's a movement. With 5 state-of-the-art training centers across the U.S. and a powerful online coaching platform, we help athletes and everyday warriors reach their next level. Whether you want to build strength, improve endurance, or transform your lifestyle — we've got your back.</p>
<a class="btn" style="left:648px;top:1802px;width:172px;height:42px">Learn More ›</a>

<div class="abs center ghost-word" style="top:1995px">SHOW</div>
<div class="abs center eyebrow" style="top:2047px">Buy merch or supplements</div>
<h2 class="abs center title" style="top:2073px">Shop Corvane</h2>
<div class="prod" style="left:116px"><div class="ph" role="img" aria-label="Product: supplement pouch" style="background:linear-gradient(160deg,#fff,#dfe3e8)"></div><h3>PRODUCT HEADING</h3><p>Lorem ipsum is simply dummy text</p><div class="price">$59.99</div></div>
<div class="prod" style="left:443px"><div class="ph" role="img" aria-label="Product: black t-shirt, cap and mug" style="left:35px;width:240px;background:linear-gradient(160deg,#2a2d31,#555a60)"></div><h3>PRODUCT HEADING</h3><p>Lorem ipsum is simply dummy text</p><div class="price">$59.99</div></div>
<div class="prod" style="left:778px"><div class="ph" role="img" aria-label="Product: protein tub" style="background:linear-gradient(160deg,#8a9097,#4a4f56)"></div><h3>PRODUCT HEADING</h3><p>Lorem ipsum is simply dummy text</p><div class="price">$59.99</div></div>
<svg class="abs" style="left:538px;top:2531px" width="100" height="44">
  <circle cx="22" cy="22" r="21" fill="#0054AA"/><path d="M30 22H14M20 16l-6 6 6 6" stroke="#fff" stroke-width="2.5" fill="none"/>
  <circle cx="76" cy="22" r="21" fill="#EE7325"/><path d="M68 22h16M78 16l6 6-6 6" stroke="#fff" stroke-width="2.5" fill="none"/>
</svg>

<section class="loc abs"></section>
<div class="abs center" style="top:2703px;font-family:Barlow,sans-serif;font-weight:700;font-size:13px;color:#fff;text-transform:uppercase">Join our gym</div>
<h2 class="abs center title" style="top:2729px;color:#fff">Our Locations</h2>
<div class="diamond" role="img" aria-label="Photo: San Diego skyline by the bay" style="left:190px;top:2849px;background:linear-gradient(135deg,#8fb6d8,#3c78a8 60%,#2d5a7a)"></div>
<div class="diamond" role="img" aria-label="Photo: Boston skyline and bridge" style="left:504px;top:2849px;background:linear-gradient(135deg,#4f8fd0,#1e4d8a 60%,#1a2e55)"></div>
<div class="diamond" role="img" aria-label="Photo: Miami skyline at sunset" style="left:823px;top:2849px;background:linear-gradient(135deg,#d89a6a,#7f6a7a 50%,#3b4a66)"></div>
<div class="diamond" role="img" aria-label="Photo: Seattle skyline at night" style="left:346px;top:3014px;background:linear-gradient(135deg,#5a3b8a,#2b2a66 55%,#1b1d3e)"></div>
<div class="diamond" role="img" aria-label="Photo: Washington DC aerial view" style="left:660px;top:3014px;background:linear-gradient(135deg,#a9b8c8,#6d8296 55%,#3f5468)"></div>
<div class="loc-name" style="left:195px;top:3016px">Sandiego</div>
<div class="loc-name" style="left:509px;top:3016px">Boston</div>
<div class="loc-name" style="left:828px;top:3016px">Miami</div>
<div class="loc-name" style="left:351px;top:3183px">Seattle</div>
<div class="loc-name" style="left:665px;top:3183px">DC</div>
<a class="btn" style="left:519px;top:3235px;width:174px;height:42px">Join the Gym ›</a>

<div class="abs" style="left:110px;top:3420px;font-size:15px;color:var(--blue-700);text-transform:uppercase">Resources</div>
<h2 class="abs title" style="left:110px;top:3447px">Latest Blogs</h2>
<article class="blog-big">
  <div class="ph" role="img" aria-label="Photo: female athlete skipping rope in a competition arena" style="left:0;top:0;width:493px;height:312px;background:linear-gradient(120deg,#16181c,#2e3238 50%,#111)"></div>
  <div class="date" style="left:0;top:286px">▦ 20 APR 2025</div>
  <div class="blog-title" style="left:38px;top:334px">Lorem ipsum dolor sit amet consect</div>
  <div class="blog-desc" style="left:38px;top:362px">Lorem ipsum dolor sit amet, consectetur adipiscing elitLorem ipsum</div>
  <a class="btn" style="left:36px;top:393px;width:138px;height:38px;font-size:11px">Learn More ›</a>
</article>
<article class="blog-sm" style="top:3524px">
  <div class="ph" role="img" aria-label="Photo: athlete training with battle ropes" style="left:0;top:0;width:217px;height:219px;background:linear-gradient(120deg,#2a2520,#6a5a4a 55%,#1e1a17)"></div>
  <div class="date" style="left:248px;top:20px">▦ 20 APR 2025</div>
  <div class="blog-title" style="left:248px;top:54px;width:230px">Lorem ipsum dolor sit amet consectetur</div>
  <div class="blog-desc" style="left:248px;top:106px;width:230px">Lorem ipsum dolor sit amet, consecte-tur adipiscing elitLorem ipsum</div>
  <a class="btn" style="left:246px;top:160px;width:128px;height:34px;font-size:11px">Learn More ›</a>
</article>
<article class="blog-sm" style="top:3760px">
  <div class="ph" role="img" aria-label="Photo: woman lifting a barbell in a gym" style="left:0;top:0;width:217px;height:219px;background:linear-gradient(120deg,#1d2d4a,#3a5a8a 55%,#15203a)"></div>
  <div class="date" style="left:248px;top:20px">▦ 20 APR 2025</div>
  <div class="blog-title" style="left:248px;top:54px;width:230px">Lorem ipsum dolor sit amet consectetur</div>
  <div class="blog-desc" style="left:248px;top:106px;width:230px">Lorem ipsum dolor sit amet, consecte-tur adipiscing elitLorem ipsum</div>
  <a class="btn" style="left:246px;top:160px;width:128px;height:34px;font-size:11px">Learn More ›</a>
</article>

<section class="news abs" role="img" aria-label="Faded background photo of athletes in a gym"></section>
<div class="abs center" style="top:4163px;font-size:15px;color:var(--blue-700);text-transform:uppercase">Stay fit. Stay connected.</div>
<h2 class="abs center title" style="top:4190px">Sign Up Newsletter</h2>
<div class="input">Email address</div>
<div class="subscribe">Subscribe <span>›</span></div>

<svg class="abs" style="left:0;top:4360px" width="1200" height="542" viewBox="0 0 1200 542">
  <polygon points="0,8 480,96 0,148" fill="#EE7325"/>
  <polygon points="0,148 1200,50 1200,542 0,542" fill="#0054AA"/>
</svg>
<div class="abs" style="left:122px;top:4575px;font-family:Barlow,sans-serif;font-weight:700;font-size:34px;line-height:47px;color:#fff;text-transform:uppercase">Corvane<br>Athletics</div>
<div class="abs foot-h" style="left:426px;top:4567px">Navigation</div>
<ul class="abs foot-list" style="left:426px;top:4601px"><li>Home</li><li>About Us</li><li>Programs</li><li>Shop</li><li>Locations</li></ul>
<ul class="abs foot-list" style="left:551px;top:4601px"><li>Affiliate</li><li>Blog</li><li>Members</li><li>Contact Us</li></ul>
<div class="abs foot-h" style="left:713px;top:4567px">Programs</div>
<ul class="abs foot-list" style="left:713px;top:4601px"><li>Masters</li><li>Functional Fitness</li><li>Competitive</li><li>Nutrition</li><li>Speciality</li><li>Hybrid Racing</li></ul>
<div class="abs foot-h" style="left:932px;top:4567px">Follow Us</div>
<div class="abs" style="left:930px;top:4592px">
  <div class="social"><i></i>Facefeed</div>
  <div class="social"><i></i>Snapgram</div>
  <div class="social"><i></i>Viewtube</div>
</div>
<div class="abs" style="left:120px;top:4816px;width:945px;border-top:2px dotted rgba(255,255,255,.45)"></div>
<svg class="abs" style="left:1065px;top:4801px" width="32" height="32"><circle cx="16" cy="16" r="15" fill="#EE7325"/><path d="M10 19l6-6 6 6" stroke="#fff" stroke-width="2.5" fill="none"/></svg>
<div class="abs" style="left:434px;top:4845px;font-size:11px;color:#e7eef8">Copyright © 2025 Corvane Athletics. All Right Reserved</div>

</body>
</html>
```